Business Cards for company that supports physicians that do medical research

Need to create a business card for Qorvel Studies (www.qorvelstudies.example), a company devoted to supporting physicians who conduct medical research. The form of the card should match the message of research and information quest. I have provided the logo of the company as an uploaded file. Designs should be simple and slick aimed at very high end clients.

Target Market(s)

Medical doctors that are also researchers

Industry/Entity Type

Medical

Contact Information for Business Card

Should feature logo and fields for personal info:
Name/title
Phone /email

Font styles to use
Serif
Sans Serif

Requirements
Must have
• Qorvel logo and fields for personal info:
• Name: Bertrand Okonfu
• Title: VP Research and Senior Analyst
• Phone: 555-203-4719
• email: info@qorvelstudies.example
Nice to have
• Interesting cards that I've seen:
• 1- all black/charcoal or very dark background
• 2- Plastic - semi-transparent
• 3- non-standard height-width ratios
• 4- Functional cards -- USB drive incorporated
Should not have
• Too busy; needs to stay very simple

```html
<!DOCTYPE html>
<html lang="en">
<head>
<meta charset="utf-8">
<title>Qorvel Studies – Business Card</title>
<link rel="stylesheet" href="https://fonts.googleapis.com/css2?family=Arimo:wght@400&display=swap">
<style>
  :root {
    --card-bg: #ffffff;
    --label-grey: #666666;
    --value-blue: #1b7ec2;
    --mark-blue: #1b7ec2;
    --brand-grey: #5f5f5f;
  }
  html, body {
    margin: 0;
    padding: 0;
    width: 1200px;
    height: 693px;
    overflow: hidden;
    background: var(--card-bg);
  }
  .business-card {
    position: relative;
    width: 1200px;
    height: 693px;
    background: var(--card-bg);
    font-family: "Arimo", Arial, sans-serif;
    overflow: hidden;
  }
  .brand {
    position: absolute;
    left: 76px;
    top: 150px;
    display: flex;
    align-items: center;
    gap: 22px;
  }
  .brand-dot {
    width: 34px;
    height: 34px;
    border-radius: 50%;
    background: var(--mark-blue);
    flex: none;
  }
  .brand-name {
    margin: 0;
    font-size: 50px;
    font-weight: 400;
    letter-spacing: 6px;
    color: var(--brand-grey);
    line-height: 1;
    white-space: nowrap;
  }
  .contact-details {
    position: absolute;
    left: 470px;
    top: 432px;
    margin: 0;
    display: grid;
    grid-template-columns: 148px auto;
    column-gap: 52px;
    row-gap: 7px;
    font-size: 33px;
    line-height: 38px;
  }
  .contact-label {
    margin: 0;
    text-align: right;
    color: var(--label-grey);
  }
  .contact-value {
    margin: 0;
    color: var(--value-blue);
    white-space: nowrap;
  }
</style>
</head>
<body>
  <main class="business-card">
    <header class="brand">
      <span class="brand-dot" aria-hidden="true"></span>
      <h1 class="brand-name">Qorvel Studies</h1>
    </header>

    <dl class="contact-details">
      <dt class="contact-label">Name</dt>
      <dd class="contact-value">Bertrand Okonfu</dd>
      <dt class="contact-label">Title</dt>
      <dd class="contact-value">VP Research and Senior Analyst</dd>
      <dt class="contact-label">Phone</dt>
      <dd class="contact-value">555-203-4719</dd>
      <dt class="contact-label">e-mail</dt>
      <dd class="contact-value">info@qorvelstudies.example</dd>
    </dl>
  </main>
</body>
</html>
```